Marwick Law Letterhead

We need a new letterhead design for a Law Firm. The address for the law firm is 1475 Calloway Street, Suite 210, Houston, Texas 77041. Phone Number: 832-361-9027; Fax Number: 832-614-7359. The logo is uploaded to the project.

```html
<!DOCTYPE html>
<html lang="en">
<head>
<meta charset="utf-8">
<title>Marwick Law Letterhead</title>
<link href="https://fonts.googleapis.com/css2?family=Montserrat:wght@400;500;600&display=swap" rel="stylesheet">
<style>
  :root {
    --bg: #e8e8e8;
    --paper: #ffffff;
    --navy: #1f2d5c;
    --red: #e01b24;
    --red-dark: #7a0a10;
    --ink: #2b2b2b;
    --ink-strong: #111111;
  }
  * { margin: 0; padding: 0; box-sizing: border-box; }
  html, body { width: 1154px; height: 1200px; overflow: hidden; background: var(--bg); }
  body { font-family: "Montserrat", sans-serif; color: var(--ink); }

  .letterhead {
    position: absolute; left: 148px; top: 0;
    width: 858px; height: 1200px;
    background: var(--paper);
  }

  .brand {
    position: absolute; left: 30px; top: 88px;
    display: flex; align-items: center; gap: 14px;
  }
  .brand-mark { width: 46px; height: 46px; border-radius: 50%; background: var(--navy); }
  .brand-name { font-size: 34px; font-weight: 600; color: var(--navy); letter-spacing: 0.5px; }

  .header-rule {
    position: absolute; left: 31px; top: 206px;
    width: 795px; height: 6px; background: var(--red);
  }

  .date {
    position: absolute; right: 33px; top: 276px;
    font-size: 16px; color: var(--ink-strong);
  }

  .recipient {
    position: absolute; left: 33px; top: 287px;
    font-size: 14.5px; line-height: 21.3px; color: var(--ink-strong);
  }

  .body {
    position: absolute; left: 34px; top: 378px; width: 795px;
    font-size: 14.3px; line-height: 21.3px; text-align: justify; color: var(--ink);
  }
  .body p + p { margin-top: 21.3px; }

  .closing {
    position: absolute; left: 31px; top: 980px;
    font-size: 17px; color: var(--ink-strong);
  }
  .signature {
    position: absolute; left: 31px; top: 1013px;
    width: 96px; height: 26px;
    background: linear-gradient(90deg, #d9d9d9, #efefef);
    border-radius: 3px;
  }

  .footer-band { position: absolute; left: 0; top: 1086px; width: 858px; height: 30px; }

  .contact {
    position: absolute; left: 0; width: 858px; text-align: center;
    font-size: 15.5px; color: var(--ink-strong);
  }
  .contact-phones { top: 1127px; display: flex; justify-content: center; align-items: center; gap: 8px; }
  .contact-phones .item { display: inline-flex; align-items: center; gap: 10px; }
  .contact-phones .item + .item { margin-left: 8px; }
  .contact-address { top: 1156px; }
</style>
</head>
<body>
  <main class="letterhead">
    <header class="brand">
      <span class="brand-mark"></span>
      <span class="brand-name">Marwick Law</span>
    </header>
    <div class="header-rule"></div>

    <div class="date">DATE:05-Jan-2022</div>

    <address class="recipient" style="font-style:normal">
      Mr/s<br>First Name and Last Name<br>Company Name<br>Address
    </address>

    <section class="body">
      <p>Lorem ipsum dolor sit amet,consectetur adipiscing sed do eiusmod tempor incididunt laboreet dolore magna aliqua.Ut enim ad minim.veniam, quis nostrud exercitation ullamco laboris nisi ut aliquip exea commodo consequat.Lorem ipsum dolor sit amet,consectetur adipiscing sed do eiusmod tempor incididunt.labore et dolore magna aliqua. Ut enim</p>
      <p>Lorem ipsum dolor sit amet, consectetur adipiscing sed do eiusmod tempor incididunt labore et dolore magna aliqua. Ut enim ad minim veniam, quis nostrud exercitation ullamco laboris nisi ut aliquip exea commodo consequat.Duis aute irure dolor in reprehenderit in voluptate velit esse cillum irure dolor in reprehenderit in voluptate velit esse irure</p>
      <p>Lorem ipsum dolor sit amet, consectetur adipiscing sed do eiusmod tempor incididunt labore et dolore magna aliqua. consequat. Duis aute irure dolor in.reprehenderit in voluptate velit esse cillum dolore eu fugiat nulla pariatur. Excepteur sint occaecat cupidatat non proident, sunt in culpa qui officia deserunt mollit,</p>
      <p>Lorem ipsum dolor sit amet, consectetur adipiscing sed do eiusmod tempor incididunt labore et dolore magna aliqua. Ut enim Lorem ipsum dolor sit amet, consectetur adipiscing sed do eiusmod tempor incididunt labore et dolore magna aliqua. Ut enim Lorem ipsum aliqua.ipsum</p>
      <p>Lorem ipsum dolor sit amet, consectetur adipiscing sed do eiusmod tempor incididunt labore et dolore magna aliqua. Ut enim ad minim veniam, quis nostrud exercitation ullamco laboris nisi ut aliquip exea commodo consequat.Duis aute irure dolor in reprehenderit in voluptate velit esse cillum irure dolor in reprehenderit in voluptate velit esse irure</p>
      <p>Lorem ipsum dolor sit amet, consectetur adipiscing sed do eiusmod tempor incididunt labore et dolore magna aliqua. Ut enim ad minim veniam, quis nostrud exercitation ullamco laboris nisi ut aliquip exea commodo consequat.Duis aute irure dolor in reprehenderit in voluptate velit esse cillum irure dolor in reprehenderit in voluptate velit esse irure</p>
    </section>

    <div class="closing">Regards</div>
    <div class="signature" role="img" aria-label="Handwritten signature of the sender"></div>

    <svg class="footer-band" viewBox="0 0 858 30" aria-hidden="true">
      <defs>
        <linearGradient id="bandGrad" x1="0" x2="1" y1="0" y2="0">
          <stop offset="0" stop-color="#e01b24"/>
          <stop offset="1" stop-color="#7a0a10"/>
        </linearGradient>
        <linearGradient id="ruleGrad" x1="0" x2="1" y1="0" y2="0">
          <stop offset="0" stop-color="#e01b24"/>
          <stop offset="1" stop-color="#7a0a10"/>
        </linearGradient>
      </defs>
      <rect x="0" y="14" width="858" height="1.5" fill="url(#ruleGrad)"/>
      <polygon points="263,1 533,1 547,28 277,28" fill="url(#bandGrad)"/>
    </svg>

    <div class="contact contact-phones">
      <span class="item">
        <svg width="14" height="14" viewBox="0 0 24 24" aria-hidden="true"><path fill="#e01b24" d="M6.6 10.8a15.1 15.1 0 0 0 6.6 6.6l2.2-2.2a1 1 0 0 1 1-.25 11.4 11.4 0 0 0 3.6.57 1 1 0 0 1 1 1V20a1 1 0 0 1-1 1A17 17 0 0 1 3 4a1 1 0 0 1 1-1h3.5a1 1 0 0 1 1 1c0 1.25.2 2.45.57 3.6a1 1 0 0 1-.25 1z"/></svg>
        832-361-9027
      </span>
      <span class="item">
        <svg width="14" height="14" viewBox="0 0 24 24" aria-hidden="true"><path fill="#e01b24" d="M6 2h12v5H6zM4 8h16a2 2 0 0 1 2 2v7h-4v5H6v-5H2v-7a2 2 0 0 1 2-2zm4 8v4h8v-4z"/></svg>
        832-614-7359
      </span>
    </div>
    <div class="contact contact-address">1475 Calloway Street, Suite 210, Houston, Texas 77041</div>
  </main>
</body>
</html>
```